Moravel Aesthetic Doctor

I require an elegant, luxurious looking business card for my aesthetic business. I am a doctor and that will set me aside from competitors. I am planning to provide home and spa based treatments to clients with high expectations. I have attached my logo.

```html
<!DOCTYPE html>
<html lang="en">
<head>
<meta charset="utf-8">
<title>Moravel Aesthetic Doctor – Business Card</title>
<link rel="stylesheet" href="https://fonts.googleapis.com/css2?family=Cinzel:wght@400&family=Libre+Baskerville:wght@700&family=Quicksand:wght@500&display=swap">
<style>
  :root {
    --bg: #e4e6e8;
    --card: #ffffff;
    --grey: #8e9093;
    --grey-light: #b9bbbd;
    --blue: #1aa3e8;
    --shadow: rgba(0,0,0,0.12);
  }
  * { margin: 0; padding: 0; box-sizing: border-box; }
  html, body { width: 1200px; height: 965px; overflow: hidden; background: var(--bg); }
  .stage { position: relative; width: 1200px; height: 965px; }
  .card {
    position: absolute; left: 100px; width: 1000px; height: 430px; overflow: hidden;
    background: var(--card); box-shadow: 0 6px 18px var(--shadow);
  }
  .card--front { top: 30px; }
  .card--back { top: 505px; }

  .brand__circle {
    display: block; border-radius: 50%; border: 4px solid var(--grey-light); flex: none;
  }
  .brand__name {
    font-family: "Cinzel", serif; font-weight: 400; color: var(--grey);
    line-height: 1; letter-spacing: 2px; white-space: nowrap;
  }
  .brand__title { display: block; }
  .brand__sub { display: block; letter-spacing: 3px; }

  /* Front */
  .brand--front { position: absolute; left: 280px; top: 95px; display: flex; align-items: center; gap: 22px; }
  .brand--front .brand__circle { width: 150px; height: 150px; }
  .brand--front .brand__title { font-size: 78px; }
  .brand--front .brand__sub { font-size: 27px; margin-top: 6px; }

  .tagline-rule {
    position: absolute; left: 60px; right: 60px; top: 320px;
    display: flex; align-items: center; gap: 18px;
  }
  .tagline-rule__line { flex: 1; height: 2px; background: var(--grey-light); }
  .tagline-rule__text {
    font-family: "Libre Baskerville", serif; font-weight: 700; font-size: 17px;
    color: var(--blue); letter-spacing: 1px; text-transform: uppercase;
  }

  /* Back */
  .brand--back .brand__circle {
    position: absolute; left: 42px; top: 292px; width: 110px; height: 110px;
  }
  .brand--back .brand__name {
    position: absolute; left: 60px; top: 278px; width: 260px;
    transform-origin: left top; transform: rotate(-90deg);
  }
  .brand--back .brand__title { font-size: 52px; }
  .brand--back .brand__sub { font-size: 17px; margin-top: 4px; color: var(--blue); }

  .person { position: absolute; left: 270px; top: 45px; }
  .person__name {
    font-family: "Libre Baskerville", serif; font-weight: 700; font-size: 30px; color: var(--grey);
  }
  .person__creds {
    font-family: "Quicksand", sans-serif; font-size: 22px; color: var(--grey);
    border-left: 2px solid var(--grey); padding-left: 10px; margin-left: 8px;
  }
  .person__diploma {
    font-family: "Quicksand", sans-serif; font-size: 21px; color: var(--grey); margin-top: 4px;
  }

  .contact { position: absolute; left: 320px; top: 175px; list-style: none; }
  .contact__item {
    display: flex; align-items: center; gap: 12px;
    font-family: "Quicksand", sans-serif; font-size: 22px; color: var(--grey); line-height: 32px;
  }
  .contact__item svg { width: 18px; height: 18px; flex: none; }
  .contact__accent { color: var(--blue); }

  .social { position: absolute; left: 760px; top: 140px; display: flex; gap: 14px; }
  .social__dot { width: 22px; height: 22px; border-radius: 50%; background: var(--blue); }

  .services {
    position: absolute; left: 320px; top: 300px; list-style: none;
    font-family: "Quicksand", sans-serif; font-size: 23px; color: var(--blue); line-height: 31px;
  }
</style>
</head>
<body>
<main class="stage">
  <section class="card card--front">
    <div class="brand brand--front">
      <span class="brand__circle"></span>
      <span class="brand__name">
        <span class="brand__title">Moravel</span>
        <span class="brand__sub">Aesthetic Doctor</span>
      </span>
    </div>
    <div class="tagline-rule">
      <span class="tagline-rule__line"></span>
      <span class="tagline-rule__text">Home and Spa Based Treatments</span>
      <span class="tagline-rule__line"></span>
    </div>
  </section>

  <section class="card card--back">
    <div class="brand brand--back">
      <span class="brand__circle"></span>
      <span class="brand__name">
        <span class="brand__title">Moravel</span>
        <span class="brand__sub">Aesthetic Doctor</span>
      </span>
    </div>

    <div class="person">
      <p><span class="person__name">Dr Lena Varga</span><span class="person__creds">MRCPCH MD</span></p>
      <p class="person__diploma">Australasian Diploma of Aesthetic Medicine</p>
    </div>

    <div class="social" aria-label="Social media">
      <span class="social__dot"></span>
      <span class="social__dot"></span>
    </div>

    <ul class="contact">
      <li class="contact__item">
        <svg viewBox="0 0 24 24" fill="none" stroke="#1aa3e8" stroke-width="2"><path d="M5 3h4l2 5-3 2a11 11 0 0 0 6 6l2-3 5 2v4a2 2 0 0 1-2 2A17 17 0 0 1 3 5a2 2 0 0 1 2-2z"/></svg>
        0800 555 014
      </li>
      <li class="contact__item">
        <svg viewBox="0 0 24 24" fill="none" stroke="#1aa3e8" stroke-width="2"><rect x="2" y="5" width="20" height="14"/><path d="M2 5l10 8 10-8"/></svg>
        lena@moravel.co.nz
      </li>
      <li class="contact__item">
        <svg viewBox="0 0 24 24" fill="none" stroke="#1aa3e8" stroke-width="2"><circle cx="12" cy="12" r="10"/><path d="M2 12h20M12 2a15 15 0 0 1 0 20M12 2a15 15 0 0 0 0 20"/></svg>
        <span>www.<span class="contact__accent">moravel</span>.co.nz</span>
      </li>
    </ul>

    <ul class="services">
      <li>Dermal injectables - Plasma facials - Microneedling</li>
      <li>Skin boosters - Excessive sweating</li>
      <li>Home and Spa Based Treatments</li>
    </ul>
  </section>
</main>
</body>
</html>
```